DJ Colm Vetter

I'm looking for a professional but still artsy/progressive design. I come from a hip hop/club DJ background playing a lot of underground music but have switched to doing more corporate parties and weddings recently. I am all about keeping the dancefloor moving and emotionally connecting with the crowd. I'd like a trendy/updated color palette. Something that's clean enough that looks professional but also trendy enough to convey that by the end of the night we'll be sweatily dancing to the latest hits. Some designers/artists I like: Tarn Olquist, Pavel Remy, Wendell Quarrie, Lumeno 7400, Silas Dravin.

```html
<!DOCTYPE html>
<html lang="en">
<head>
<meta charset="utf-8">
<title>DJ Colm Vetter – Business Card</title>
<link href="https://fonts.googleapis.com/css2?family=Cinzel:wght@600&family=Lato:wght@400&display=swap" rel="stylesheet">
<style>
  :root {
    --backdrop: #2b2b2c;
    --card: #1d1e20;
    --card-edge: #26272a;
    --white: #f4f4f4;
    --grey-text: #c9c9c9;
    --rule: #5a5a5c;
    --red: #d2141b;
    --green: #6cab1f;
  }
  * { margin: 0; padding: 0; box-sizing: border-box; }
  html, body {
    width: 1200px; height: 1108px; overflow: hidden;
    background: var(--backdrop);
  }
  .stage {
    position: relative; width: 1200px; height: 1108px;
    display: flex; justify-content: center; align-items: center; gap: 60px;
  }
  .card {
    position: relative; width: 420px; height: 660px;
    border-radius: 28px; background: var(--card);
    box-shadow: 0 18px 40px rgba(0,0,0,0.45);
    overflow: hidden;
  }
  .wordmark {
    font-family: "Cinzel", serif; font-weight: 600;
    color: var(--white); font-size: 40px; letter-spacing: 1px;
    white-space: nowrap; text-align: center;
  }
  .card-front .wordmark { position: absolute; top: 150px; left: 0; right: 0; }
  .holder { position: absolute; top: 330px; left: 0; right: 0; text-align: center; }
  .holder-name {
    font-family: "Cinzel", serif; font-weight: 600;
    color: var(--red); font-size: 27px; letter-spacing: 1px;
  }
  .holder-role {
    font-family: "Lato", sans-serif; color: var(--green); font-size: 18px; margin-top: 2px;
  }
  .icon-row {
    position: absolute; top: 410px; left: 60px; right: 60px;
    display: flex; align-items: center; gap: 10px;
  }
  .icon-row .rule { flex: 1; height: 1px; background: var(--rule); }
  .icon-row svg { width: 22px; height: 22px; display: block; }
  .contact {
    position: absolute; top: 446px; left: 0; right: 0; text-align: center;
    font-family: "Lato", sans-serif; color: var(--grey-text);
    font-size: 19px; line-height: 26px;
  }
  .contact .divider { width: 300px; height: 1px; background: var(--rule); margin: 10px auto; }
  .back-pattern {
    position: absolute; inset: 0;
    background: linear-gradient(135deg, var(--card-edge) 0%, var(--card) 60%, #18191b 100%);
  }
  .card-back .wordmark { position: absolute; bottom: 90px; left: 0; right: 0; }
</style>
</head>
<body>
<main class="stage">
  <section class="card card-front">
    <div class="wordmark">DJ Colm Vetter</div>
    <div class="holder">
      <div class="holder-name">Marcus Ellory</div>
      <div class="holder-role">Managing Director</div>
    </div>
    <div class="icon-row">
      <span class="rule"></span>
      <svg viewBox="0 0 22 22" aria-label="phone"><circle cx="11" cy="11" r="11" fill="var(--red)"/><path d="M7.5 6h2l1 2.5-1.3 1a6 6 0 0 0 3.3 3.3l1-1.3 2.5 1v2a1 1 0 0 1-1 1A9 9 0 0 1 6.5 7a1 1 0 0 1 1-1z" fill="#fff"/></svg>
      <svg viewBox="0 0 22 22" aria-label="email"><circle cx="11" cy="11" r="11" fill="var(--red)"/><rect x="5.5" y="7.5" width="11" height="7.5" fill="#fff"/><path d="M5.5 7.5l5.5 4 5.5-4" stroke="var(--red)" stroke-width="1.2" fill="none"/></svg>
      <svg viewBox="0 0 22 22" aria-label="website"><circle cx="11" cy="11" r="11" fill="var(--red)"/><g stroke="#fff" stroke-width="1.2" fill="none"><circle cx="11" cy="11" r="5.5"/><ellipse cx="11" cy="11" rx="2.3" ry="5.5"/><path d="M5.5 11h11"/></g></svg>
      <span class="rule"></span>
    </div>
    <div class="contact">
      <div>444 555 7021</div>
      <div>book@colmvetter.mix</div>
      <div>www.colmvetter.mix</div>
      <div class="divider"></div>
      <div>87, Harlow Street,</div>
      <div>Brennmoor,30918</div>
    </div>
  </section>

  <section class="card card-back">
    <div class="back-pattern" role="img" aria-label="Faint repeating name pattern across the card back"></div>
    <div class="wordmark">DJ Colm Vetter</div>
  </section>
</main>
</body>
</html>
```